Website for software company "velora"

We need a website for our software company/startup named "velora". We are developing several products (currently 3 standard-software products) which are all in different sectors, but all our products are available for Laptops/PC/Mobile Phones/Tablets, ... We do also create custom software and support our customers with consulting to optimize their processes.
We already have a Logo which you can find in the attached files.
We are a young team of 4 members (two founders and 2 employees).

To get an idea of our products -> the first one is a planning software for healthcare organizations (eg. BlueHaven, firebrigade, pharmacy), the second one is a booking software for sport clubs and the third one is a competition software for sports hunting. You see very diverse. Include or ignore this info of our products as you like.

The design has to be a bootstrap 4 (or higher) design. We have licenced FontAwesome as iconset. Responsive design should come without saying.

• Starting page, product pages, news section, contact, team, services

```html
<!DOCTYPE html>
<html lang="en">
<head>
<meta charset="utf-8">
<title>velora – Our Products</title>
<link href="https://fonts.googleapis.com/css2?family=Poppins:wght@400;500;600;700;800&display=swap" rel="stylesheet">
<style>
:root{
  --orange:#f47b2a;
  --orange-soft:#fdf1e9;
  --ink:#262a35;
  --text:#4a4e57;
  --muted:#8a8f99;
  --grey-bg:#f2f2f3;
  --line:#e4e4e6;
  --white:#ffffff;
  --footer:#262a35;
  --footer-text:#c9ccd3;
}
*{box-sizing:border-box;margin:0;padding:0}
html,body{width:1200px;height:3512px;overflow:hidden}
body{position:relative;background:var(--white);font-family:'Poppins',sans-serif;color:var(--ink)}
.abs{position:absolute}
.brand{font-family:'Poppins',sans-serif;font-weight:600;color:var(--ink);line-height:1;white-space:nowrap}

/* header */
.site-header .brand{left:89px;top:24px;font-size:42px}
.main-nav{font-size:13px;font-weight:500;color:var(--ink)}
.main-nav a{position:absolute;white-space:nowrap;text-decoration:none;color:inherit}
.main-nav a.active{color:var(--orange);font-weight:600}
.nav-active-bar{left:541px;top:0;width:100px;height:3px;background:var(--orange)}
.btn-contact{left:982px;top:25px;width:128px;height:40px;border:2px solid var(--ink);border-radius:20px;font-size:13px;font-weight:600;display:flex;align-items:center;justify-content:center}

.page-title{left:0;width:1200px;top:122px;text-align:center;font-size:57px;font-weight:700;line-height:1.2}
.page-sub{left:0;width:1200px;top:203px;text-align:center;font-size:17px;color:var(--text)}

.blob{border-radius:50%;background:var(--orange-soft)}

.mock{border-radius:14px;background:linear-gradient(135deg,#f6f7f9,#e8eaef)}
.mock-frame{border:3px solid var(--ink)}
.float-card{background:var(--white);border-radius:10px;box-shadow:0 8px 30px rgba(0,0,0,.1)}

.product-title{left:746px;top:326px;width:420px;font-size:33px;font-weight:700;line-height:40px}
.product-text{left:746px;top:426px;width:380px;font-size:15px;line-height:23px;color:var(--text)}
.btn-orange{background:var(--orange);color:var(--white);border-radius:24px;font-size:13px;font-weight:600;display:flex;align-items:center;justify-content:center}

.band-title{left:0;width:1200px;top:876px;text-align:center;color:var(--white);font-size:33px;font-weight:700;line-height:41px}
.skill{font-size:14px;font-weight:600;color:var(--white);line-height:22px}
.skill.left{text-align:right;width:240px;left:128px}
.skill.right{left:806px;width:240px}
.skill-icon{width:44px;height:44px}
.center-disc{left:458px;top:990px;width:256px;height:256px;border-radius:50%;background:var(--white);display:flex;align-items:center;justify-content:center;font-size:40px;font-weight:600;color:var(--orange)}

.steps-title{left:89px;top:1398px;width:440px;font-size:33px;font-weight:700;line-height:40px}
.acc-item{left:89px;width:405px;height:56px;border-bottom:1px solid var(--line);display:flex;justify-content:space-between;align-items:center;font-size:15px;font-weight:500}
.acc-item .plus{color:var(--orange);font-size:20px;font-weight:400}

.hire-title{left:0;width:1200px;top:2048px;text-align:center;font-size:33px;font-weight:700}
.hire-sub{left:0;width:1200px;top:2092px;text-align:center;font-size:17px;font-weight:600}
.hire-card{top:2149px;width:216px;height:213px;background:var(--white);border-radius:6px;box-shadow:0 6px 24px rgba(0,0,0,.06);display:flex;flex-direction:column;align-items:center}
.hire-card svg{margin-top:28px}
.hire-card p{position:absolute;top:132px;width:100%;text-align:center;font-size:15px;font-weight:600;line-height:22px}

.faq-title{left:0;width:1200px;top:2534px;text-align:center;font-size:33px;font-weight:700}
.faq-item{left:209px;width:781px;height:67px;border-bottom:2px solid var(--line);display:flex;justify-content:space-between;align-items:center;font-size:15px;font-weight:500}
.faq-item .plus{color:var(--orange);font-size:20px}

.footer-head{font-size:20px;font-weight:700;color:var(--white)}
.footer-list{list-style:none;font-size:13px;color:var(--footer-text);line-height:31px}
.footer-list li::before{content:"›";margin-right:8px;color:var(--muted)}
.contact-row{font-size:13px;line-height:18px;color:var(--footer-text);left:893px;width:240px}
.social{width:38px;height:38px;border-radius:50%;background:#3a3e49}
.footer-rule{left:89px;top:3454px;width:1020px;height:1px;background:#3d414c}
.copyright{left:0;width:1200px;top:3472px;text-align:center;font-size:13px;font-weight:600;color:var(--white)}
.to-top{left:1131px;top:3432px;width:42px;height:42px;border-radius:50%;background:var(--orange);display:flex;align-items:center;justify-content:center}
</style>
</head>
<body>

<div class="abs blob" style="left:-130px;top:228px;width:480px;height:480px"></div>
<svg class="abs" style="left:0;top:0" width="1200" height="3512" aria-hidden="true">
  <polygon points="0,907 1200,702 1200,1319 0,1319" fill="var(--orange)"/>
  <polygon points="0,1834 1200,2045 1200,2448 0,2448" fill="var(--grey-bg)"/>
  <polygon points="0,3160 1200,2925 1200,2952 0,3191" fill="#c9cbd0"/>
  <polygon points="0,3191 1200,2952 1200,3512 0,3512" fill="var(--footer)"/>
</svg>
<div class="abs blob" style="left:910px;top:1740px;width:420px;height:300px;opacity:.8"></div>

<header class="site-header">
  <div class="abs brand">velora</div>
  <div class="abs nav-active-bar"></div>
  <nav class="abs main-nav" style="left:0;top:36px">
    <a style="left:479px">HOME</a>
    <a class="active" style="left:541px">OUR PRODUCT</a>
    <a style="left:664px">OUR SERVICES</a>
    <a style="left:781px">OUR TEAM</a>
    <a style="left:871px">LATEST NEWS</a>
  </nav>
  <div class="abs btn-contact">CONTACT</div>
</header>

<h1 class="abs page-title">Our Products</h1>
<p class="abs page-sub">Our products are available for Laptops/PC Mobile Phones/Tablets, ...</p>

<div class="abs mock mock-frame" style="left:85px;top:327px;width:576px;height:350px" role="img" aria-label="Screenshot of the clinic planning dashboard with visit charts and upcoming visits"></div>
<div class="abs float-card" style="left:45px;top:652px;width:239px;height:65px" role="img" aria-label="Notification card about a cancelled patient visit"></div>
<div class="abs float-card" style="left:507px;top:513px;width:175px;height:49px" role="img" aria-label="Highlighted upcoming visit card"></div>

<h2 class="abs product-title">Software for healthcare organizations</h2>
<p class="abs product-text">Lorem ipsum dolor sit amet, consectetur adipiscing elit. Aenean sodales dictum viverra. Nam gravida dignissim eros. Vivamus congue erat ante, volutpat dictum neque dignissim eget. Aenean sollicitudin, lorem quis bibendum auctor, nisi elit consequat ipsum, nec sagittis sem nibh id elit duis sed odio sit amet nibh vulputate...</p>
<div class="abs btn-orange" style="left:746px;top:614px;width:195px;height:42px">DISCUS YOUR PROJECT</div>

<h2 class="abs band-title">Hire Web Design<br>and Development Experts</h2>
<div class="abs center-disc">velora</div>

<div class="abs skill left" style="top:1010px">Prototyping &amp; UI/UX<br>Designing</div>
<div class="abs skill left" style="top:1094px">Progressive Web<br>Development</div>
<div class="abs skill left" style="top:1181px">Custom Website<br>Development</div>
<div class="abs skill right" style="top:1010px">Full Stack<br>Development</div>
<div class="abs skill right" style="top:1094px">API<br>Development</div>
<div class="abs skill right" style="top:1181px">Upgradation and<br>Migration</div>

<svg class="abs skill-icon" style="left:384px;top:1010px" viewBox="0 0 44 44" fill="none" stroke="#fff" stroke-width="2"><path d="M4 40 L4 4 L40 40 Z"/><path d="M10 30 L10 22 L18 30 Z"/><path d="M4 12h5M4 20h5M4 28h5"/></svg>
<svg class="abs skill-icon" style="left:384px;top:1094px" viewBox="0 0 44 44" fill="none" stroke="#fff" stroke-width="2"><rect x="2" y="4" width="40" height="36" rx="2"/><path d="M2 12h40"/><circle cx="22" cy="27" r="7"/><circle cx="22" cy="27" r="2.5"/></svg>
<svg class="abs skill-icon" style="left:384px;top:1181px" viewBox="0 0 44 44" fill="none" stroke="#fff" stroke-width="2"><rect x="2" y="6" width="40" height="32" rx="2"/><path d="M2 13h40M16 20l-6 6 6 6M28 20l6 6-6 6M24 18l-4 16"/></svg>
<svg class="abs skill-icon" style="left:747px;top:1010px" viewBox="0 0 44 44" fill="none" stroke="#fff" stroke-width="2"><path d="M22 4 L40 13 L22 22 L4 13 Z"/><path d="M4 21 L22 30 L40 21M4 29 L22 38 L40 29"/></svg>
<svg class="abs skill-icon" style="left:747px;top:1094px" viewBox="0 0 44 44" fill="none" stroke="#fff" stroke-width="2"><rect x="2" y="4" width="40" height="36" rx="2"/><rect x="8" y="12" width="28" height="18" rx="2"/><text x="22" y="26" fill="#fff" stroke="none" font-size="10" font-family="Poppins,sans-serif" font-weight="700" text-anchor="middle">API</text></svg>
<svg class="abs skill-icon" style="left:747px;top:1181px" viewBox="0 0 44 44" fill="none" stroke="#fff" stroke-width="2"><rect x="2" y="6" width="34" height="32" rx="2"/><path d="M2 13h34M19 32V18M14 23l5-5 5 5"/><circle cx="36" cy="32" r="6"/></svg>

<h2 class="abs steps-title">How Web Development Outsourcing With Velora Works?</h2>
<div class="abs acc-item" style="top:1531px">Discuss Your Requirements<span class="plus">+</span></div>
<div class="abs acc-item" style="top:1587px">Get a Proposal<span class="plus">+</span></div>
<div class="abs acc-item" style="top:1643px">Web Development and Designing<span class="plus">+</span></div>
<div class="abs acc-item" style="top:1698px">Quality Assurance<span class="plus">+</span></div>
<div class="abs acc-item" style="top:1754px;border-bottom:none">Project Launch<span class="plus">+</span></div>

<div class="abs mock" style="left:577px;top:1411px;width:530px;height:377px;box-shadow:0 10px 30px rgba(0,0,0,.08)" role="img" aria-label="Screenshot of the doctor scheduling app with profile, calendar and patient table">
  <div style="position:absolute;left:0;top:0;width:42px;height:100%;background:var(--ink);border-radius:14px 0 0 14px"></div>
</div>

<h2 class="abs hire-title">Hire Dedicated Web Developers</h2>
<p class="abs hire-sub">Choose How You Want to Collaborate</p>

<div class="abs hire-card" style="left:153px">
  <svg width="68" height="76" viewBox="0 0 68 76" fill="none" stroke="var(--orange)" stroke-width="2.5"><rect x="14" y="4" width="50" height="68" rx="4"/><path d="M24 16h30M24 24h30M24 32h30"/><path d="M22 58l10-10 8 6 14-14"/><path d="M4 40h14M4 52h14M7 40l7 12M14 40l-7 12"/></svg>
  <p>Project-Based</p>
</div>
<div class="abs hire-card" style="left:379px">
  <svg width="72" height="72" viewBox="0 0 72 72" fill="none" stroke="var(--orange)" stroke-width="2.5"><circle cx="36" cy="36" r="33"/><path d="M36 10v26l-8 12"/><path d="M36 6v5M36 61v5M6 36h5M61 36h5"/></svg>
  <p>Hire Developers on<br>Hourly Basis</p>
</div>
<div class="abs hire-card" style="left:604px">
  <svg width="110" height="62" viewBox="0 0 110 62" fill="none" stroke="var(--orange)" stroke-width="2.5"><circle cx="55" cy="16" r="13"/><circle cx="22" cy="24" r="10"/><circle cx="88" cy="24" r="10"/><path d="M32 60c0-16 10-26 23-26s23 10 23 26"/><path d="M4 60c0-12 7-20 18-20 5 0 8 1 11 4M106 60c0-12-7-20-18-20-5 0-8 1-11 4"/></svg>
  <p>Dedicated Team<br>of Developers</p>
</div>
<div class="abs hire-card" style="left:830px">
  <svg width="72" height="72" viewBox="0 0 72 72" fill="none" stroke="var(--orange)" stroke-width="2.5"><circle cx="36" cy="36" r="33"/><path d="M26 28c0-6 4-10 10-10s10 4 10 9c0 7-10 8-10 16"/><circle cx="36" cy="52" r="1.5" fill="var(--orange)"/></svg>
  <p>I'm not sure</p>
</div>

<h2 class="abs faq-title">Frequently Asked Questions</h2>
<div class="abs faq-item" style="top:2599px">1. What's the difference between website design and development?<span class="plus">+</span></div>
<div class="abs faq-item" style="top:2666px">2. What is included in website development?<span class="plus">+</span></div>
<div class="abs faq-item" style="top:2732px">3. What programming languages do web developers use?<span class="plus">+</span></div>
<div class="abs faq-item" style="top:2798px">4. How much does building a website typically cost?<span class="plus">+</span></div>
<div class="abs faq-item" style="top:2865px;border-bottom:none">5. What's the difference between website design and development?<span class="plus">+</span></div>

<footer>
  <div class="abs brand" style="left:156px;top:3240px;font-size:50px;color:var(--white)">velora</div>
  <div class="abs social" style="left:187px;top:3307px" aria-label="Social profile"></div>
  <div class="abs social" style="left:236px;top:3307px" aria-label="Social profile"></div>
  <div class="abs social" style="left:285px;top:3307px" aria-label="Social profile"></div>
  <div class="abs social" style="left:333px;top:3307px" aria-label="Social profile"></div>

  <h3 class="abs footer-head" style="left:464px;top:3175px">Quick Links</h3>
  <ul class="abs footer-list" style="left:464px;top:3218px">
    <li>Home</li><li>Our Product</li><li>Our Services</li><li>Our Team</li><li>Latest news</li><li>Contact Us</li>
  </ul>
  <h3 class="abs footer-head" style="left:660px;top:3175px">Information</h3>
  <ul class="abs footer-list" style="left:660px;top:3218px">
    <li>Privacy Policy</li><li>Terms &amp; Conditions</li><li>Shipping Policy</li><li>FAQ's</li><li>Sitemap</li><li>Blog</li>
  </ul>
  <h3 class="abs footer-head" style="left:870px;top:3175px">Contact info</h3>

  <svg class="abs" style="left:871px;top:3226px" width="14" height="11" viewBox="0 0 14 11"><rect width="14" height="11" rx="1" fill="var(--orange)"/><path d="M1 1l6 5 6-5" stroke="var(--footer)" stroke-width="1.5" fill="none"/></svg>
  <div class="abs contact-row" style="top:3225px">Email:<br>hello@velora.io</div>
  <svg class="abs" style="left:871px;top:3280px" width="14" height="14" viewBox="0 0 24 24"><path fill="var(--orange)" d="M6.6 10.8a15 15 0 0 0 6.6 6.6l2.2-2.2a1 1 0 0 1 1-.25 11.4 11.4 0 0 0 3.6.57 1 1 0 0 1 1 1V20a1 1 0 0 1-1 1A17 17 0 0 1 3 4a1 1 0 0 1 1-1h3.5a1 1 0 0 1 1 1c0 1.25.2 2.450.57 3.57a1 1 0 0 1-.25 1z"/></svg>
  <div class="abs contact-row" style="top:3279px">Phone:<br>08 555-014-2290</div>
  <svg class="abs" style="left:872px;top:3333px" width="12" height="16" viewBox="0 0 12 16"><path fill="var(--orange)" d="M6 0a6 6 0 0 0-6 6c0 4.5 6 10 6 10s6-5.5 6-10a6 6 0 0 0-6-6zm0 8.5A2.5 2.5 0 1 1 6 3.5a2.5 2.5 0 0 1 0 5z"/></svg>
  <div class="abs contact-row" style="top:3331px">Location:<br>Some address line goes<br>here city name country</div>

  <div class="abs footer-rule"></div>
  <div class="abs copyright">© Copyright 2022 Velora, All Rights Reserved</div>
  <div class="abs to-top"><svg width="12" height="14" viewBox="0 0 12 14" fill="none" stroke="#fff" stroke-width="1.5"><path d="M6 13V1M1 6l5-5 5 5"/></svg></div>
</footer>

</body>
</html>
```